Lifecoach needs website design based on a standard Wordpress theme

I need a website for my new lifecoaching business that can be easily implemented in Wordpress, it needs to be compatible with a standard Wordpress theme. So I can place the pictures, texts etc. in a standard theme of Wordpress.

I want the design to be a very good feeling and playfull one, based on my logo.

Target Market(s)

I will coach people to reach their goals and dreams in life.

Industry/Entity Type

Business

Requirements
Must have
• Can be easy implemented in Wordpress.
Nice to have
• Photo's of nature are nice.

```html
<!DOCTYPE html>
<html lang="en">
<head>
<meta charset="utf-8">
<title>Lena Brightwater Lifecoach</title>
<link href="https://fonts.googleapis.com/css2?family=Lato:wght@300;400;700&display=swap" rel="stylesheet">
<style>
:root{
  --navy:#0d4f80;
  --navy-deep:#093e66;
  --footer:#0c5385;
  --blue:#1a9ad6;
  --sky:#1ab4ee;
  --heading:#1a5a8a;
  --ink:#333;
  --muted:#9aa3ab;
  --page:#eef3f7;
  --white:#fff;
}
*{box-sizing:border-box;margin:0;padding:0}
html,body{width:1024px;height:1200px;overflow:hidden}
body{font-family:'Lato',sans-serif;background:var(--page);position:relative;color:var(--ink)}
.abs{position:absolute}

.topbar{left:0;top:0;width:1024px;height:32px;background:var(--navy)}
.topbar-contact{right:122px;top:9px;display:flex;gap:20px;font-size:9px;color:var(--white);align-items:center}
.topbar-contact span{display:flex;align-items:center;gap:6px}

.header{left:0;top:32px;width:1024px;height:72px;background:var(--white)}
.brand{left:120px;top:0;width:270px;height:94px;background:linear-gradient(#fafafa,#dcdfe2);border:1px solid #c9ccd0;border-top:none;box-shadow:0 2px 3px rgba(0,0,0,.2);display:flex;align-items:center;gap:10px;padding-left:12px;z-index:2}
.brand-mark{width:64px;height:64px;border-radius:50%;background:var(--blue);flex:none}
.brand-name{font-size:16px;font-weight:400;color:var(--blue);line-height:1.25;white-space:nowrap;text-align:center}
.nav{right:122px;top:28px;display:flex;gap:37px;font-size:12px;color:#555}
.nav .active{color:var(--blue)}

.hero{left:0;top:104px;width:1024px;height:384px;background:linear-gradient(180deg,#c9d6e0 0%,#e6ecf1 40%,#f3f5f7 62%,#8b959c 82%,#2f3336 100%)}
.hero-quote{left:130px;top:160px;font-size:23px;font-weight:300;line-height:33px;color:#2f6088;white-space:nowrap}
.hero-quote b{font-weight:700;color:#1a4f7a}
.dots{left:132px;top:457px;display:flex;gap:8px}
.dots i{width:8px;height:8px;border-radius:50%;background:var(--sky)}
.dots i.on{background:var(--white)}

.welcome{left:0;top:514px;width:1024px;text-align:center;font-size:25px;font-weight:300;color:var(--ink)}
.welcome b{font-weight:700;color:var(--sky)}

.feature{top:568px;width:245px}
.feature-img{height:144px}
.feature h3{margin-top:12px;font-size:15px;font-weight:400;color:var(--heading)}
.feature p{margin-top:5px;font-size:10px;line-height:16px;color:var(--muted)}

.news{left:662px;top:564px;width:240px}
.news-title{display:flex;align-items:center;gap:8px;font-size:15px;color:var(--heading);padding-left:2px}
.news-rule{margin-top:12px;height:4px;border-top:1px dotted #aaa;border-bottom:1px dotted #aaa}
.news-item{margin-top:9px}
.news-item h4{font-size:12px;font-weight:400;color:#222}
.news-row{display:flex;gap:14px;margin-top:7px}
.news-thumb{width:68px;height:58px;flex:none}
.news-row p{font-size:9px;line-height:14.5px;color:#666}
.news-date{display:block;margin-top:4px;font-size:8px;color:#555}

.testimonials{left:0;top:821px;width:1024px;height:175px;background:linear-gradient(180deg,#bfd0dd 0%,#e9eef2 55%,#dfe5ea 85%,#4d555b 100%)}
.testimonials h2{position:absolute;top:24px;width:100%;text-align:center;font-size:20px;font-weight:300;color:#333}
.person{top:69px;display:flex;gap:14px}
.avatar{width:40px;height:40px;background:#8d6d5b}
.person-name{font-size:15px;font-weight:300;color:#333;white-space:nowrap}
.person-role{font-size:10px;color:#666;margin-top:3px}
.bubble{top:65px;width:202px;height:87px;background:var(--sky);border-radius:2px;padding:14px 16px 0 36px;font-size:10.5px;font-weight:400;line-height:19px;color:var(--white)}
.bubble::before{content:"";position:absolute;left:-10px;top:20px;border:10px solid transparent;border-left:0;border-right-color:var(--sky)}
.bubble .q{position:absolute;left:14px;top:10px;font-size:22px;font-weight:700}

.footer{left:0;top:996px;width:1024px;height:162px;background:var(--footer);color:var(--white)}
.footer-brand{left:120px;top:26px;display:flex;align-items:center;gap:8px}
.footer-brand .brand-mark{width:42px;height:42px;background:var(--white)}
.footer-brand .brand-name{font-size:12px;color:var(--white)}
.footer-about{left:120px;top:96px;width:170px;font-size:10px;line-height:16px;color:#a8c3d8}
.footer h5{font-size:13px;font-weight:700}
.contact{left:318px;top:26px}
.contact ul{list-style:none;margin-top:16px;font-size:11px}
.contact li{display:flex;gap:12px;margin-bottom:8px;line-height:16px}
.contact svg{flex:none;margin-top:2px}
.newsletter{left:499px;top:26px;width:202px}
.newsletter p{margin-top:18px;font-size:10px;line-height:16px;color:#a8c3d8}
.signup{display:flex;margin-top:12px;height:29px}
.signup span{flex:1;background:#0b2c45;font-size:11px;color:#ccd;padding:8px 0 0 10px}
.signup b{width:70px;background:var(--sky);font-size:11px;font-weight:400;text-align:center;padding-top:8px}
.social{left:726px;top:26px}
.social-row{display:flex;gap:13px;margin-top:16px}
.social-row i{width:26px;height:26px;border-radius:50%;background:#0a3f69}

.bottombar{left:0;top:1158px;width:1024px;height:42px;background:var(--navy-deep);font-size:11px;color:#8ea6ba}
.copyright{left:120px;top:14px}
.bottom-nav{right:122px;top:14px;display:flex;gap:37px}
.bottom-nav .active{color:var(--white)}
</style>
</head>
<body>

<div class="abs topbar">
  <div class="abs topbar-contact">
    <span><svg width="18" height="11" viewBox="0 0 18 11"><rect x="4" y="0.5" width="13" height="10" fill="none" stroke="#9fc3e0"/><path d="M4 1l6.5 5 6.5-5" fill="none" stroke="#9fc3e0"/><path d="M0 3h3M1 6h2" stroke="#9fc3e0"/></svg>hello@brightwater-coach.test</span>
    <span><svg width="13" height="13" viewBox="0 0 13 13"><path d="M3 1l2 3-1.5 1.5c.8 1.8 2 3 3.8 3.8L9 7.8l3 2-1.5 2.2C5.5 11.5 1.5 7.5 1 2.5z" fill="#9fc3e0"/></svg>+1800.555.0142</span>
  </div>
</div>

<div class="abs header">
  <nav class="abs nav">
    <span class="active">Home</span><span>Services</span><span>Blog</span><span>About</span><span>Contact</span>
  </nav>
</div>
<div class="abs brand">
  <div class="brand-mark"></div>
  <div class="brand-name">LENA BRIGHTWATER<br>LIFECOACH</div>
</div>

<section class="abs hero" role="img" aria-label="Photograph of snow-covered mountain peaks under a cloudy sky with a dark forested slope"></section>
<p class="abs hero-quote">“The pain you feel today is the <b>strength</b> you<br>feel tomorrow. For every challenge encountered<br>there is <b>opportunity for growth.</b>”</p>
<div class="abs dots"><i></i><i class="on"></i><i></i><i></i></div>

<h1 class="abs welcome" style="font-weight:300">Welcome to <b>Lena Brightwater</b> Life Coach</h1>

<article class="abs feature" style="left:120px">
  <div class="feature-img" role="img" aria-label="Photograph of three people in a friendly conversation at an office table" style="background:linear-gradient(90deg,#5a4a40,#c8b89a 50%,#3b3a3c)"></div>
  <h3>About Us</h3>
  <p>Lorem ipsum dolor sit amet, consectetur adipisicing elit, sed do eiusmod tempor incididunt ut labore et dolore magna aliqua.</p>
</article>
<article class="abs feature" style="left:389px">
  <div class="feature-img" role="img" aria-label="Photograph of two women smiling and talking in a bright room" style="background:linear-gradient(90deg,#6b5448,#e9ecee 45%,#f4f4f2 70%,#d6c0a8)"></div>
  <h3>Services</h3>
  <p>Lorem ipsum dolor sit amet, consectetur adipisicing elit, sed do eiusmod tempor incididunt ut labore et dolore magna aliqua.</p>
</article>

<aside class="abs news">
  <div class="news-title"><svg width="16" height="16" viewBox="0 0 16 16"><rect x="1" y="3" width="14" height="12" fill="none" stroke="#1a5a8a" stroke-width="1.5"/><path d="M1 6h14M5 1v4M11 1v4" stroke="#1a5a8a" stroke-width="1.5"/></svg>Latest News</div>
  <div class="news-rule"></div>
  <div class="news-item">
    <h4>There are many variations of passages</h4>
    <div class="news-row">
      <div class="news-thumb" role="img" aria-label="Photograph of business people in a meeting" style="background:linear-gradient(135deg,#d9dde0,#5b6670)"></div>
      <p>The point of using Lorem Ipsum is that it has a more-or-less normal distribution of letters, as opposed..<span class="news-date">▦ 8 December 2013</span></p>
    </div>
  </div>
  <div class="news-item" style="margin-top:14px">
    <h4>All the Lorem Ipsum generators</h4>
    <div class="news-row">
      <div class="news-thumb" role="img" aria-label="Photograph of colleagues reviewing documents at a desk" style="background:linear-gradient(135deg,#2c3034,#c4cbd0)"></div>
      <p>The point of using Lorem Ipsum is that it has a more-or-less normal distribution of letters, as opposed..<span class="news-date">▦ 8 December 2013</span></p>
    </div>
  </div>
</aside>

<section class="abs testimonials" role="img" aria-label="Faint photograph of snowy mountains behind the testimonials">
  <h2>Client Testimonials</h2>
  <div class="abs person" style="left:140px">
    <div class="avatar" role="img" aria-label="Client portrait"></div>
    <div><div class="person-name">Tom Halvorsen</div><div class="person-role">Businessman</div></div>
  </div>
  <div class="abs bubble" style="left:298px"><span class="q">“</span>Mauris urnaei elit, mattis non urna acem, ullamcorper vula putatem lorem.</div>
  <div class="abs person" style="left:544px">
    <div class="avatar" role="img" aria-label="Client portrait" style="background:#7a4a38"></div>
    <div><div class="person-name">Maria Ostrand</div><div class="person-role">Housewife</div></div>
  </div>
  <div class="abs bubble" style="left:702px"><span class="q">“</span>Mauris urnaei elit, mattis non urna acem, ullamcorper vula putatem lorem.</div>
</section>

<footer class="abs footer">
  <div class="abs footer-brand">
    <div class="brand-mark"></div>
    <div class="brand-name">LENA BRIGHTWATER<br>LIFECOACH</div>
  </div>
  <p class="abs footer-about">Donec volutpat, mi vel egestas eleifend, dolor arcu iaculis nunc. Fusce gravida tortor felis, ac dictum risus</p>
  <div class="abs contact">
    <h5>Contact Details</h5>
    <ul>
      <li><svg width="12" height="12" viewBox="0 0 13 13"><path d="M3 1l2 3-1.5 1.5c.8 1.8 2 3 3.8 3.8L9 7.8l3 2-1.5 2.2C5.5 11.5 1.5 7.5 1 2.5z" fill="#7d9fbd"/></svg>+1800-555-0142</li>
      <li><svg width="12" height="10" viewBox="0 0 12 10"><rect x=".5" y=".5" width="11" height="9" fill="none" stroke="#7d9fbd"/><path d="M.5 1l5.5 4 5.5-4" fill="none" stroke="#7d9fbd"/></svg>hello@brightwater-coach.test</li>
      <li><svg width="12" height="14" viewBox="0 0 12 14"><path d="M6 0a5 5 0 0 1 5 5c0 4-5 9-5 9S1 9 1 5a5 5 0 0 1 5-5z" fill="#7d9fbd"/><circle cx="6" cy="5" r="2" fill="#0c5385"/></svg>Your Address, Your Country<br>Your Zip Code</li>
    </ul>
  </div>
  <div class="abs newsletter">
    <h5>Newsletter</h5>
    <p>Ipsum dolor sit amet, teft consecte tur adipiscing elit ut eunt.</p>
    <div class="signup"><span>Email Address</span><b>Subscribe</b></div>
  </div>
  <div class="abs social">
    <h5>Get Social</h5>
    <div class="social-row" aria-label="Social links"><i></i><i></i><i></i><i></i></div>
  </div>
</footer>

<div class="abs bottombar">
  <div class="abs copyright">Copyright © 2014 - LENA BRIGHTWATER. All Rights reserved</div>
  <nav class="abs bottom-nav"><span class="active">Home</span><span>Services</span><span>Blog</span><span>About</span><span>Contact</span></nav>
</div>

</body>
</html>
```